Brightmoor - a website to encourage people to spend time in nature

I have a squarespace site with some content on it but the squarespace template doesn't completely suit my needs, I keep fiddling with the template but actually I need some professional help to get it looking the way I want and with the right 'mood'.
The website is for "Brightmoor" - it will be a blog where I write about the importance of nature for good health. I also want to use the website to market services such as outdoor coaching, retreats and walking workshops.
This has been in my head for a LONG time and I currently only use instagram for micro-blogs but it's time for me to get this moving. I've previously engaged other designers on branding for it but they just didn't get it quite the way that I wanted it and I wasn't completely happy with the results. It's been a process for me as to what I want but in the meantime I just didn't come back to the design aspect of it now. I'm looking for a designer who understands the purpose of the website, the ethos and can help me realise this into a design that's clean, clear and simple.

Please note that I have a domain (brightmoor.org) and a lot of content drafted on squarespace already. I have published it with password protection - password is brightmoor2020 - it still has some of the original template on it, but does have some content. Don't take it as anything to follow in particular, i am looking for fresh eyes and fresh ideas.

Target Market(s)

There are three main groups that I want to target - people who are suffering from stress and anxiety, people who treat them and parents who want to get their kids outside (thereby preventing stress and anxiety)

Contact Information for Business Card

Joan Petrie
Brightmoor
Telephone +44 7700 900417
brightmoor@mailvane.com

Logo Text

Brightmoor - if that. I have an idea that the logo should have a leaf on it somewhere, or maybe just be a leaf.

Coding

Coded - Design and coding required

Number of Pages Required

5+ page

Font styles to use
Serif
Sans Serif

Colors
add136
33b8a4
34a6d7
3377b5

Requirements
Must have
• Space for lots of images. The ability for me to edit the pages if I need to. Be user friendly. Look beautiful.
• For an idea of the images I use and the content I'm interested in writing about have a look at @brightmoor on instagram.
• That pop up about cookies so I am complying with data laws.
Should not have
• Must not be too 'busy' I'd like to avoid too much movement.

```html
<!DOCTYPE html>
<html lang="en">
<head>
<meta charset="utf-8">
<title>Brightmoor — Home</title>
<link rel="stylesheet" href="https://fonts.googleapis.com/css2?family=Cinzel:wght@400;600&family=Poppins:wght@400;500;600&family=Lato:ital,wght@1,700&display=swap">
<style>
  :root{
    --board:#a4a4a4;
    --white:#ffffff;
    --blue:#2b63ad;
    --blue-footer:#2c64b0;
    --teal:#2aa58d;
    --leaf:#3aa86f;
    --ink:#3b3b3b;
    --cookie-blue:#2f5fae;
    --shade:rgba(4,6,12,.82);
  }
  *{box-sizing:border-box;margin:0;padding:0}
  html,body{width:1200px;height:2454px;overflow:hidden}
  body{background:var(--board);font-family:"Poppins",sans-serif;color:var(--ink);position:relative}

  .site{position:absolute;top:32px;width:538px;height:2381px;background:var(--white);overflow:hidden;display:flex;flex-direction:column}
  .site--consent{left:43px}
  .site--default{left:616px}

  .nav{height:43px;flex:none;display:flex;align-items:center;padding:0 50px;position:relative;background:var(--white)}
  .nav-group{display:flex;gap:22px;font-size:7px;font-weight:500;color:var(--blue);letter-spacing:.2px}
  .nav-group--right{margin-left:auto}
  .brand{position:absolute;left:50%;top:50%;transform:translate(-50%,-50%);display:flex;flex-direction:column;align-items:center;gap:3px}
  .brand-dot{width:14px;height:14px;border-radius:50%;background:var(--leaf)}
  .brand-name{font-family:"Cinzel",serif;font-size:7px;letter-spacing:1.6px;color:var(--leaf)}

  .photo{position:absolute;inset:0}
  .btn{display:inline-block;border-radius:10px;font-size:6.5px;font-weight:500;padding:3px 9px;line-height:10px}
  .btn--outline{border:1px solid var(--teal);color:var(--teal)}
  .btn--light{border:1px solid var(--white);color:var(--white)}
  .btn--solid{background:var(--teal);color:var(--white);padding:4px 10px}

  .heading{font-family:"Cinzel",serif;font-weight:600;color:var(--blue);font-size:13.5px;letter-spacing:.6px}
  .copy{font-size:5.6px;line-height:12.6px;text-align:justify}

  .hero{height:270px;flex:none;position:relative;color:var(--white);text-align:center}
  .hero .photo{background:linear-gradient(180deg,#8d9690 0%,#4d5a43 35%,#37452b 65%,#5f7a3a 100%)}
  .hero-content{position:relative;padding-top:86px}
  .hero-kicker{font-size:6.5px;letter-spacing:.3px}
  .hero-title{font-family:"Cinzel",serif;font-size:25px;font-weight:600;letter-spacing:1px;margin-top:2px}
  .hero-tagline{font-family:"Lato",sans-serif;font-style:italic;font-weight:700;font-size:8px;line-height:12px;margin:3px auto 9px;width:190px}

  .blog{height:296px;flex:none;padding:34px 50px 0;text-align:center}
  .blog-grid{display:grid;grid-template-columns:repeat(3,136px);gap:15px;margin-top:9px;text-align:left}
  .card-photo{height:99px;position:relative}
  .card-title{font-size:8px;font-weight:600;color:var(--blue);line-height:12.5px;margin:8px 0 3px}
  .card-copy{font-size:5.6px;line-height:12.6px;margin-bottom:5px}

  .banner{height:175px;flex:none;position:relative;color:var(--white)}
  .banner-content{position:absolute;right:50px;top:34px;width:235px;text-align:right}
  .banner .heading{color:var(--white);font-weight:400;font-size:13px;margin-bottom:3px}
  .banner .copy{text-align:justify;text-align-last:right}
  .banner .btn{margin-top:6px}
  .walking .photo{background:linear-gradient(180deg,#4a5568 0%,#a08672 38%,#c9a070 50%,#5c6a7a 70%,#3a4150 100%)}
  .retreat .photo{background:linear-gradient(180deg,#5f8183 0%,#4d7274 60%,#3a5049 100%)}

  .split{flex:none;display:flex;justify-content:space-between;padding:0 50px;position:relative}
  .split-text{width:205px}
  .split-text .heading{margin-bottom:8px}
  .split-text .btn{margin-top:9px}
  .split-photo{width:205px;height:133px;position:relative}
  .coaching{height:211px;padding-top:39px}
  .coaching .split-text{padding-top:10px}
  .about{height:199px;padding-top:28px}
  .about .split-text{padding-top:10px}
  .coaching .split-photo{background:linear-gradient(180deg,#8fa6b5 0%,#3f6f96 30%,#2d5a80 100%)}
  .about .split-photo{background:linear-gradient(90deg,#6f6c66 0%,#8a8278 45%,#b59a84 75%,#4a4844 100%)}
  .slider-arrow{position:absolute;top:53px;width:12px;height:22px;background:rgba(255,255,255,.25);display:flex;align-items:center;justify-content:center}
  .slider-arrow--prev{left:0}.slider-arrow--next{right:0}

  .contact{height:169px;flex:none;position:relative;color:var(--white);text-align:center}
  .contact .photo{background:linear-gradient(180deg,#3a4a32 0%,#4b4a3c 40%,#4a3f7a 70%,#3e3575 100%)}
  .contact-content{position:relative;padding-top:32px;width:270px;margin:0 auto}
  .contact .heading{color:var(--white);font-weight:400;font-size:13px}
  .contact-copy{font-size:6.8px;line-height:12.6px;margin:2px 0 8px}

  .subscribe{height:132px;flex:none;text-align:center;padding-top:34px}
  .subscribe-note{font-size:5.8px;margin:3px 0 8px}
  .subscribe-form{display:flex;justify-content:center;gap:6px}
  .subscribe-input{width:134px;height:21px;border:1px solid #ccc;font-size:5.6px;color:#999;text-align:left;padding:7px 7px}
  .subscribe .btn{border-radius:11px;line-height:13px;padding:3px 10px;font-size:6.5px}

  .gallery{flex:none;display:grid;grid-template-columns:346px 192px;grid-template-rows:186px 185px 184px;}
  .gallery > div{position:relative}
  .g-beach{grid-row:1/3;background:linear-gradient(180deg,#7fb0e0 0%,#a8c9e6 34%,#4a4a4a 38%,#5b534b 100%)}
  .g-coast{background:linear-gradient(180deg,#9fc4e6 0%,#8aa1b0 60%,#55575a 100%)}
  .g-lane{background:linear-gradient(180deg,#6f8a46 0%,#4f6a33 60%,#7a6a6a 100%)}
  .g-row{grid-column:1/3;display:grid;grid-template-columns:270px 268px}
  .g-leaf{background:linear-gradient(135deg,#3a5a3a 0%,#2b4a2e 60%,#4c6b44 100%)}
  .g-woods{background:linear-gradient(180deg,#2f4a24 0%,#577a2f 55%,#3c5a26 100%)}

  .footer{height:156px;flex:none;background:var(--blue-footer);color:var(--white);text-align:center;padding-top:30px}
  .footer-links{font-size:5.8px;font-weight:500;display:flex;justify-content:center;gap:4px}
  .footer .brand{position:static;transform:none;margin:17px 0 6px}
  .footer .brand-dot{width:22px;height:22px;background:var(--white)}
  .footer .brand-name{color:var(--white);font-size:9px}
  .footer-address{font-family:"Lato",sans-serif;font-style:italic;font-weight:700;font-size:7.5px}
  .footer-legal{font-size:5.5px;margin-top:20px}

  .consent-shade{position:absolute;inset:0;background:var(--shade);z-index:2}
  .cookie-notice{position:absolute;top:148px;left:0;width:538px;text-align:center;color:var(--white);z-index:3}
  .cookie-message{font-size:10.5px;font-weight:500;line-height:13px}
  .cookie-link{display:inline-block;font-size:6.5px;text-decoration:underline;margin:10px 0 9px}
  .cookie-accept{display:block;margin:0 auto;width:84px;height:23px;border-radius:12px;background:var(--cookie-blue);font-size:6.5px;font-weight:500;line-height:23px}
</style>
</head>
<body>

<!-- consent state -->
<div class="site site--consent">
  <nav class="nav">
    <div class="nav-group"><span>HOME</span><span>ABOUT</span><span>GALLERY</span></div>
    <div class="brand"><span class="brand-dot"></span><span class="brand-name">BRIGHTMOOR</span></div>
    <div class="nav-group nav-group--right"><span>BLOG</span><span>TESTIMONIALS</span><span>CONTACT</span></div>
  </nav>
  <header class="hero">
    <div class="photo" role="img" aria-label="Forest path between tall pine trees"></div>
  </header>
  <section class="blog">
    <h2 class="heading">LATEST BLOG</h2>
    <div class="blog-grid">
      <article><div class="card-photo" style="background:linear-gradient(180deg,#2d3a4a,#6a5a44)" role="img" aria-label="Wild swimmers in a dark river"></div><h3 class="card-title">Why being outside is good for the planet</h3><p class="card-copy">Lorem ipsum dolor sit amet, consectetur adipiscing elit, sed do eiusmod tempor incididunt ut labore et dolore</p><span class="btn btn--outline">Learn More</span></article>
      <article><div class="card-photo" style="background:linear-gradient(180deg,#b8bcc4,#6f7a52)" role="img" aria-label="Walker on a moorland path under cloud"></div><h3 class="card-title">Lorem ipsum dolor sit aelit, sdo eiusmod tempor</h3><p class="card-copy">Lorem ipsum dolor sit amet, consectetur adipiscing elit, sed do eiusmod tempor incididunt ut labore et dolore</p><span class="btn btn--outline">Learn More</span></article>
      <article><div class="card-photo" style="background:linear-gradient(180deg,#9bb3cc,#5d7a3a)" role="img" aria-label="Child among wild flowers"></div><h3 class="card-title">Lorem ipsum dolor sit aelit, sdo eiusmod tempor</h3><p class="card-copy">Lorem ipsum dolor sit amet, consectetur adipiscing elit, sed do eiusmod tempor incididunt ut labore et dolore</p><span class="btn btn--outline">Learn More</span></article>
    </div>
  </section>
  <section class="banner walking">
    <div class="photo" role="img" aria-label="Two walkers on a beach at sunset with birds"></div>
    <div class="banner-content"><h2 class="heading">BRIGHTMOOR WALKING</h2><p class="copy">Brightmoor Walking is an initiative aimed at getting people back into nature in the most gentlest of ways - by taking a walk with friends in the great outdoors. The concept is simple - schedule a walk outside, once a week with two or three other people.</p><span class="btn btn--light">Learn More</span></div>
  </section>
  <section class="split coaching">
    <div class="split-text"><h2 class="heading">OUTDOOR COACHING</h2><p class="copy">Only one thing better than coaching and that's coaching in the great outdoors. We believe that being out in nature gives you a greater sense of perspective when working through issues and figuring out life's path. We are part of nature, not apart from it. We are of</p><span class="btn btn--outline">Learn More</span></div>
    <div class="split-photo" role="img" aria-label="Swimmers wading into the sea"></div>
  </section>
  <section class="banner retreat">
    <div class="photo" role="img" aria-label="Swimmer climbing down a ladder into the sea"></div>
    <div class="banner-content"><h2 class="heading">RETREAT</h2><p class="copy">Sometimes you just need to get away from it all. And that's where Brightmoor retreats come in. Our retreats are based at Heathfold Cottage located at the foot of the Harrowgill Fells in beautiful Lanmoor Vale. Typically 2/3 days that involve restoring your connection.</p><span class="btn btn--light">Learn More</span></div>
  </section>
  <section class="split about">
    <div class="split-text"><h2 class="heading">ABOUT BRIGHTMOOR</h2><p class="copy">Brightmoor springs from a simple concept — the idea that spending time in nature is good for you. We don't do enough of it and we should do more if we want to be happier and healthier inhabitants of Planet Earth. Our mission is to get people of all ages outdoors as a means to feel better.</p><span class="btn btn--outline">Learn More</span></div>
    <div class="split-photo" role="img" aria-label="Portrait on a pebble shore"></div>
  </section>
  <section class="contact">
    <div class="photo" role="img" aria-label="Bluebell wood"></div>
    <div class="contact-content"><h2 class="heading">CONTACT</h2><p class="contact-copy">Lorem ipsum dolor sit amet, consectetur adipiscing elit, sed do eiusmod tempor incididunt ut labore et dolore magna aliqua. Quis ipsum suspendisse ultrices gravida. Risus commodo viverra maecenas accumsan lacus vel facilisis</p><span class="btn btn--light">Inquire</span></div>
  </section>
  <section class="subscribe">
    <h2 class="heading">SUBSCRIBE</h2>
    <p class="subscribe-note">Sign up with your email address to receive news and updates.</p>
    <div class="subscribe-form"><span class="subscribe-input">Email Address</span><span class="btn btn--outline">SIGN UP</span></div>
  </section>
  <section class="gallery">
    <div class="g-beach" role="img" aria-label="Dog on a beach with a long shadow"></div>
    <div class="g-coast" role="img" aria-label="Child looking out to sea"></div>
    <div class="g-lane" role="img" aria-label="Tree-lined country lane"></div>
    <div class="g-row"><div class="g-leaf" role="img" aria-label="Ladybird on a leaf"></div><div class="g-woods" role="img" aria-label="Walker in a green wood"></div></div>
  </section>
  <footer class="footer">
    <div class="footer-links"><span>ABOUT</span><span>CONNECT</span><span>TERMS &amp; POLICIES</span></div>
    <div class="brand"><span class="brand-dot"></span><span class="brand-name">BRIGHTMOOR</span></div>
    <p class="footer-address">(888) 888-8888 • 777 Your Location. New York, NY 00000</p>
    <p class="footer-legal">Copyright © 2020. All Rights Reserved</p>
  </footer>
  <div class="consent-shade"></div>
  <div class="cookie-notice">
    <p class="cookie-message">We uses cookies to make your<br>experience on this website better.</p>
    <span class="cookie-link">Cookie Policies</span>
    <span class="cookie-accept">ACCEPT COOKIES</span>
  </div>
</div>

<!-- default state -->
<div class="site site--default">
  <nav class="nav">
    <div class="nav-group"><span>HOME</span><span>ABOUT</span><span>GALLERY</span></div>
    <div class="brand"><span class="brand-dot"></span><span class="brand-name">BRIGHTMOOR</span></div>
    <div class="nav-group nav-group--right"><span>BLOG</span><span>TESTIMONIALS</span><span>CONTACT</span></div>
  </nav>
  <header class="hero">
    <div class="photo" role="img" aria-label="Forest path between tall pine trees"></div>
    <div class="hero-content">
      <p class="hero-kicker">WELCOME</p>
      <h1 class="hero-title">BRIGHTMOOR</h1>
      <p class="hero-tagline">The Practice Of Feeling Better By Spending Time In Nature.</p>
      <span class="btn btn--solid">Our Story</span>
    </div>
  </header>
  <section class="blog">
    <h2 class="heading">LATEST BLOG</h2>
    <div class="blog-grid">
      <article><div class="card-photo" style="background:linear-gradient(180deg,#2d3a4a,#6a5a44)" role="img" aria-label="Wild swimmers in a dark river"></div><h3 class="card-title">Why being outside is good for the planet</h3><p class="card-copy">Lorem ipsum dolor sit amet, consectetur adipiscing elit, sed do eiusmod tempor incididunt ut labore et dolore</p><span class="btn btn--outline">Learn More</span></article>
      <article><div class="card-photo" style="background:linear-gradient(180deg,#b8bcc4,#6f7a52)" role="img" aria-label="Walker on a moorland path under cloud"></div><h3 class="card-title">Lorem ipsum dolor sit aelit, sdo eiusmod tempor</h3><p class="card-copy">Lorem ipsum dolor sit amet, consectetur adipiscing elit, sed do eiusmod tempor incididunt ut labore et dolore</p><span class="btn btn--outline">Learn More</span></article>
      <article><div class="card-photo" style="background:linear-gradient(180deg,#9bb3cc,#5d7a3a)" role="img" aria-label="Child among wild flowers"></div><h3 class="card-title">Lorem ipsum dolor sit aelit, sdo eiusmod tempor</h3><p class="card-copy">Lorem ipsum dolor sit amet, consectetur adipiscing elit, sed do eiusmod tempor incididunt ut labore et dolore</p><span class="btn btn--outline">Learn More</span></article>
    </div>
  </section>
  <section class="banner walking">
    <div class="photo" role="img" aria-label="Two walkers on a beach at sunset with birds"></div>
    <div class="banner-content"><h2 class="heading">BRIGHTMOOR WALKING</h2><p class="copy">Brightmoor Walking is an initiative aimed at getting people back into nature in the most gentlest of ways - by taking a walk with friends in the great outdoors. The concept is simple - schedule a walk outside, once a week with two or three other people.</p><span class="btn btn--light">Learn More</span></div>
  </section>
  <section class="split coaching">
    <div class="split-text"><h2 class="heading">OUTDOOR COACHING</h2><p class="copy">Only one thing better than coaching and that's coaching in the great outdoors. We believe that being out in nature gives you a greater sense of perspective when working through issues and figuring out life's path. We are part of nature, not apart from it. We are of</p><span class="btn btn--outline">Learn More</span></div>
    <div class="split-photo" role="img" aria-label="Swimmers wading into the sea">
      <span class="slider-arrow slider-arrow--prev"><svg width="6" height="10" viewBox="0 0 6 10"><path d="M5 1 1 5l4 4" fill="none" stroke="#fff" stroke-width="1"/></svg></span>
      <span class="slider-arrow slider-arrow--next"><svg width="6" height="10" viewBox="0 0 6 10"><path d="m1 1 4 4-4 4" fill="none" stroke="#fff" stroke-width="1"/></svg></span>
    </div>
  </section>
  <section class="banner retreat">
    <div class="photo" role="img" aria-label="Swimmer climbing down a ladder into the sea"></div>
    <div class="banner-content"><h2 class="heading">RETREAT</h2><p class="copy">Sometimes you just need to get away from it all. And that's where Brightmoor retreats come in. Our retreats are based at Heathfold Cottage located at the foot of the Harrowgill Fells in beautiful Lanmoor Vale. Typically 2/3 days that involve restoring your connection.</p><span class="btn btn--light">Learn More</span></div>
  </section>
  <section class="split about">
    <div class="split-text"><h2 class="heading">ABOUT BRIGHTMOOR</h2><p class="copy">Brightmoor springs from a simple concept — the idea that spending time in nature is good for you. We don't do enough of it and we should do more if we want to be happier and healthier inhabitants of Planet Earth. Our mission is to get people of all ages outdoors as a means to feel better.</p><span class="btn btn--outline">Learn More</span></div>
    <div class="split-photo" role="img" aria-label="Portrait on a pebble shore"></div>
  </section>
  <section class="contact">
    <div class="photo" role="img" aria-label="Bluebell wood"></div>
    <div class="contact-content"><h2 class="heading">CONTACT</h2><p class="contact-copy">Lorem ipsum dolor sit amet, consectetur adipiscing elit, sed do eiusmod tempor incididunt ut labore et dolore magna aliqua. Quis ipsum suspendisse ultrices gravida. Risus commodo viverra maecenas accumsan lacus vel facilisis</p><span class="btn btn--light">Inquire</span></div>
  </section>
  <section class="subscribe">
    <h2 class="heading">SUBSCRIBE</h2>
    <p class="subscribe-note">Sign up with your email address to receive news and updates.</p>
    <div class="subscribe-form"><span class="subscribe-input">Email Address</span><span class="btn btn--outline">SIGN UP</span></div>
  </section>
  <section class="gallery">
    <div class="g-beach" role="img" aria-label="Dog on a beach with a long shadow"></div>
    <div class="g-coast" role="img" aria-label="Child looking out to sea"></div>
    <div class="g-lane" role="img" aria-label="Tree-lined country lane"></div>
    <div class="g-row"><div class="g-leaf" role="img" aria-label="Ladybird on a leaf"></div><div class="g-woods" role="img" aria-label="Walker in a green wood"></div></div>
  </section>
  <footer class="footer">
    <div class="footer-links"><span>ABOUT</span><span>CONNECT</span><span>TERMS &amp; POLICIES</span></div>
    <div class="brand"><span class="brand-dot"></span><span class="brand-name">BRIGHTMOOR</span></div>
    <p class="footer-address">(888) 888-8888 • 777 Your Location. New York, NY 00000</p>
    <p class="footer-legal">Copyright © 2020. All Rights Reserved</p>
  </footer>
</div>

</body>
</html>
```